Brightline Energy Product Distribution Brochure

We are looking to have our current brochure for our customers completely redesigned...the idea is to present the relevant information in an attractive way . Our website is brightlineenergyco.example where you can find more information about us. We have included a file with a rough idea of the page order and what each should include but feel free to adapt based on design. The example provided is only for context and doesnt have to be maintained. We will be using the brochure both digitally and in print form. As long as it reads easily and is eye catching, the design can be horizontal or vertical.Final deliverable should be indesign file.

"Our Brands" page: should be limited to one page (space being enough) where it has the header for each one (for example diesel generators) space for one or two lines of text and then the corresponding logos for each of the five categories
Updates

For those asking: the "our brands" page should be a single page layout where there is a header with the corresponding section and space for maybe one line of text followed by the two logos for that category. Each of the product pages should be similar in fashion to the one in the document attached: a photo of the product with some white space and space for the text to be included. We will be posting additional examples today

Target Market(s)

We want to present it to customers both digitally and in print so they can see our products

Industry/Entity Type

Power Generation

Font styles to use
Serif

Requirements
Must have
• Eye catching and able to present the information in a presentable fashion. Rest is up to you.
Nice to have
• Should incorporate the colors of our logo but can also add other depending on design

```html
<!DOCTYPE html>
<html lang="en">
<head>
<meta charset="utf-8">
<title>Brightline Energy – Our Stock / Our Products</title>
<link href="https://fonts.googleapis.com/css2?family=Montserrat:wght@300;400;700;800&display=swap" rel="stylesheet">
<style>
  :root {
    --yellow: #f5c518;
    --yellow-deep: #e0ad10;
    --grey-bar: #6d6a68;
    --grey-dark: #3b3835;
    --ink: #4a4744;
    --paper: #ffffff;
    --backdrop: #e7e6e3;
  }
  * { box-sizing: border-box; margin: 0; padding: 0; }
  html, body { width: 1200px; height: 960px; overflow: hidden; }
  body {
    background: var(--backdrop);
    font-family: "Montserrat", Arial, sans-serif;
    position: relative;
  }
  .spread {
    position: absolute;
    left: 40px; top: 240px;
    width: 1120px; height: 480px;
    background: var(--paper);
    box-shadow: 0 10px 30px rgba(0,0,0,.15);
    overflow: hidden;
  }
  .spread-art { position: absolute; inset: 0; }
  .fold {
    position: absolute; left: 559px; top: 0; width: 2px; height: 100%;
    background: rgba(0,0,0,.08);
  }
  .stock-title {
    position: absolute; left: 70px; top: 40px;
    font-weight: 800; font-size: 30px; letter-spacing: .5px; line-height: 1.2;
    color: var(--yellow-deep);
  }
  .stock-list { position: absolute; left: 70px; top: 88px; width: 290px; list-style: none; }
  .stock-item {
    position: relative; height: 46px; margin-bottom: 8px;
    background: var(--grey-bar); overflow: hidden;
    color: #efeeec; font-weight: 300; font-size: 10.5px; line-height: 1.3;
    padding: 9px 88px 0 10px;
  }
  .stock-item--tall { height: 58px; padding-top: 7px; }
  .stock-tag {
    position: absolute; right: 0; top: 0; width: 88px; height: 100%;
    background: var(--yellow);
    clip-path: polygon(58% 0, 82% 0, 42% 100%, 18% 100%);
  }
  .stock-tag-label {
    position: absolute; right: 22px; top: 50%;
    width: 48px; text-align: center;
    font-size: 9.5px; font-weight: 700; color: #fff; line-height: 1;
    transform: translateY(-50%) rotate(-50deg);
  }
  .stock-copy {
    position: absolute; left: 70px; top: 378px; width: 300px;
    display: flex; gap: 14px;
    font-size: 7.4px; line-height: 1.45; color: var(--ink); font-weight: 400;
  }
  .stock-copy p { flex: 1; }
  .stock-copy strong { font-weight: 700; }
  .products-title {
    position: absolute; left: 770px; top: 332px;
    font-weight: 800; font-size: 26px; color: #fff; letter-spacing: .5px; line-height: 1.2;
  }
</style>
</head>
<body>
  <main class="spread">
    <svg class="spread-art" viewBox="0 0 1120 480" width="1120" height="480">
      <defs>
        <linearGradient id="engineTone" x1="0" y1="0" x2="1" y2="1">
          <stop offset="0" stop-color="#8a8478"/>
          <stop offset=".35" stop-color="#c9a02a"/>
          <stop offset=".7" stop-color="#6b5a2a"/>
          <stop offset="1" stop-color="#2f2c28"/>
        </linearGradient>
      </defs>
      <rect class="accent-block" x="460" y="160" width="130" height="290" fill="var(--yellow)"/>
      <polygon class="engine-photo" role="img" aria-label="Close-up photograph of a diesel generator engine with yellow tint"
        points="290,0 1010,0 1120,190 1120,480 820,480 600,420 470,160"
        fill="url(#engineTone)"/>
      <rect class="products-panel" x="750" y="40" width="280" height="350" fill="var(--yellow)" opacity=".82"/>
      <polygon class="corner-dark" points="1120,320 1120,480 1060,480" fill="var(--grey-dark)"/>
    </svg>
    <div class="fold"></div>

    <h1 class="stock-title">OUR STOCK</h1>
    <ul class="stock-list">
      <li class="stock-item">20+ generator trailers from<br>3500 to 10400 LBS capacity.<span class="stock-tag"></span><span class="stock-tag-label">in stock</span></li>
      <li class="stock-item">50+ Fuel Tanks from<br>50 to 1000 Gal<span class="stock-tag"></span><span class="stock-tag-label">in stock</span></li>
      <li class="stock-item">100+ Automatic Transfer<br>Switches from 100 to 2000 AMPS<span class="stock-tag"></span><span class="stock-tag-label">in stock</span></li>
      <li class="stock-item">50+ Diesel Generators from<br>20 to 500 KW<span class="stock-tag"></span><span class="stock-tag-label">in stock</span></li>
      <li class="stock-item stock-item--tall">1000+ Engine parts, Alternator parts, Generator parts, Automatic Voltage Regulators and Generator controls<span class="stock-tag"></span><span class="stock-tag-label">in stock</span></li>
    </ul>
    <div class="stock-copy">
      <p><strong>BRIGHTLINE ENERGY</strong> offers you one of the largest inventories in North America of industrial generator sets to meet even the most urgent needs. Additionally, our company carries the single largest stock of Automatic Voltage Regulators and Automatic Transfer</p>
      <p>Switches in the United States with 1000+ units of all major brands ready to ship SAME DAY to any country in the world. We understand your urgency and we understand "same day". Our friendly staff will assist you same day, we will quote same day and we will ship <strong>SAME DAY</strong>.</p>
    </div>

    <h2 class="products-title">OUR PRODUCTS</h2>
  </main>
</body>
</html>
```